Business Card Design - ChoiceCraft

Looking for creative, modern design, two sided for ChoiceCraft that is consistent with color and feel of website www.choicecraftpro.net.
Updates

Back of card will be used to promote products or have a quote revolving around decisions, change, leadership, innovation, creativity. Back should also have space to promote website, but optional to use the icon. Front of the card will need to use the icon and have standard place for name, job title, phone and email. We are not looking to put a mailing address or fax. Also want space to place a few words/phrase explaining what we do...such as individual growth and organizational development or tools, training, information...in addition, want the facebook icon small on the front somewhere as we are also on facebook.

Vector file uploaded of icon.

Target Market(s)

Professional coaching for individual growth and organizational development

Industry/Entity Type

Business

Requirements
Must have
• Icon...see attached.

```html
<!DOCTYPE html>
<html lang="en">
<head>
<meta charset="utf-8">
<title>ChoiceCraft Business Card</title>
<link rel="stylesheet" href="https://fonts.googleapis.com/css2?family=Arimo:wght@400;700&display=swap">
<style>
  :root {
    --stage: #e6e8eb;
    --card: #ffffff;
    --ink: #2b2b2b;
    --ink-soft: #3a3a3a;
    --brand-blue: #2a8fd6;
    --sky: #39b3ec;
    --sky-light: #7fd0f5;
    --navy: #2c3a8c;
    --rule: #8a8a8a;
    --mark: #bcd9ef;
    --mark-edge: #2a8fd6;
  }
  * { margin: 0; padding: 0; box-sizing: border-box; }
  html, body { width: 1200px; height: 1053px; overflow: hidden; }
  body {
    background: var(--stage);
    font-family: "Arimo", Arial, sans-serif;
    color: var(--ink);
    position: relative;
  }
  .card {
    position: absolute;
    width: 766px;
    height: 436px;
    background: var(--card);
    box-shadow: 0 2px 6px rgba(0,0,0,0.25);
    overflow: hidden;
  }
  .card-front { left: 63px; top: 41px; }
  .card-back { left: 312px; top: 540px; }

  /* Front */
  .brand-mark {
    position: absolute;
    left: 121px; top: 90px;
    width: 176px; height: 176px;
    border-radius: 50%;
    background: radial-gradient(circle at 45% 40%, #e9f3fb, var(--mark));
    border: 6px solid var(--mark-edge);
  }
  .brand-name {
    position: absolute;
    left: 0; width: 450px; top: 286px;
    text-align: center;
    font-weight: 700;
    font-size: 33px;
    letter-spacing: 0.5px;
    color: #111;
  }
  .divider {
    position: absolute;
    left: 389px; top: 142px;
    width: 3px; height: 188px;
    background: linear-gradient(to bottom, #ddd, var(--rule), #ddd);
  }
  .person {
    position: absolute;
    left: 413px; top: 160px;
    font-size: 25px;
    font-weight: 700;
    color: var(--ink);
  }
  .person .title { font-weight: 400; font-size: 18px; }
  .contacts {
    position: absolute;
    left: 413px; top: 216px;
    list-style: none;
    font-size: 20px;
    color: var(--ink-soft);
  }
  .contacts li {
    height: 26px;
    display: flex;
    align-items: center;
    gap: 8px;
  }
  .contacts svg { width: 14px; height: 14px; flex: none; }
  .social-square {
    width: 12px; height: 12px;
    background: #3b5998;
    display: inline-block;
    margin: 0 1px;
  }
  .tagline {
    position: absolute;
    left: 66px; top: 384px;
    font-size: 19px;
    color: var(--ink-soft);
  }
  .band {
    position: absolute;
    left: 0; bottom: 0;
    width: 766px; height: 16px;
  }

  /* Back */
  .quotes {
    position: absolute;
    left: 40px; top: 34px;
    list-style: none;
  }
  .quote {
    position: relative;
    height: 77px;
    padding-left: 68px;
  }
  .quote-mark {
    position: absolute;
    left: 0; top: 4px;
    width: 32px; height: 32px;
    border-radius: 50%;
    background: radial-gradient(circle at 45% 40%, #e9f3fb, var(--mark));
    border: 3px solid var(--mark-edge);
  }
  .quote-text {
    font-size: 19px;
    color: var(--ink);
    line-height: 26px;
  }
  .quote-text .q {
    font-weight: 700;
    font-size: 30px;
    line-height: 0;
    vertical-align: -6px;
    margin: 0 2px;
  }
  .quote-text .q-open { vertical-align: 2px; margin-left: -22px; margin-right: 4px; }
  .quote-text .q-close { vertical-align: -12px; }
  .quote-author {
    font-size: 19px;
    color: var(--ink);
    margin-top: 2px;
  }
  .quote-author strong { color: var(--brand-blue); font-weight: 700; }
  .back-mark {
    position: absolute;
    left: 562px; top: 238px;
    width: 164px; height: 164px;
    border-radius: 50%;
    background: radial-gradient(circle at 45% 40%, #e9f3fb, var(--mark));
    border: 6px solid var(--mark-edge);
  }
</style>
</head>
<body>

<section class="card card-front">
  <div class="brand-mark" role="img" aria-label="Plain circle beside the company name"></div>
  <div class="brand-name">ChoiceCraft</div>
  <div class="divider"></div>
  <div class="person">Your Name, <span class="title">Title</span></div>
  <ul class="contacts">
    <li>
      <svg viewBox="0 0 14 14" aria-hidden="true"><path d="M3 1l3 3-1.5 1.5a8 8 0 0 0 4 4L10 8l3 3-2 2C6 13 1 8 1 3z" fill="#333"/></svg>
      123-456-789
    </li>
    <li>
      <svg viewBox="0 0 14 14" aria-hidden="true"><rect x="1" y="3" width="12" height="8" fill="none" stroke="#333" stroke-width="1.5"/><path d="M1 3l6 5 6-5" fill="none" stroke="#333" stroke-width="1.5"/></svg>
      hello@choicecraftpro.net
    </li>
    <li>
      <svg viewBox="0 0 14 14" aria-hidden="true"><circle cx="7" cy="7" r="6" fill="none" stroke="#333" stroke-width="1.3"/><path d="M1 7h12M7 1c-3 3-3 9 0 12M7 1c3 3 3 9 0 12" fill="none" stroke="#333" stroke-width="1"/></svg>
      www.choicecraftpro.net
    </li>
    <li>
      <span class="social-square" aria-hidden="true"></span>
      /choicecraftpro
    </li>
  </ul>
  <p class="tagline">Supporting individual growth and&nbsp; organizational development.</p>
  <svg class="band" viewBox="0 0 766 16" preserveAspectRatio="none" aria-hidden="true">
    <defs>
      <linearGradient id="bandSky" x1="0" x2="1">
        <stop offset="0" stop-color="#2a7fd0"/>
        <stop offset="0.6" stop-color="#39b3ec"/>
        <stop offset="1" stop-color="#bfe8fb"/>
      </linearGradient>
    </defs>
    <polygon points="0,4 370,4 360,16 0,16" fill="url(#bandSky)"/>
    <polygon points="380,0 766,0 766,16 366,16" fill="#2c3a8c"/>
  </svg>
</section>

<section class="card card-back">
  <ul class="quotes">
    <li class="quote">
      <span class="quote-mark" aria-hidden="true"></span>
      <p class="quote-text"><span class="q q-open">“</span>Try not to become a man of success, but rather a man of value.<span class="q q-close">”</span></p>
      <p class="quote-author">- <strong>Anton Ellery</strong></p>
    </li>
    <li class="quote">
      <span class="quote-mark" aria-hidden="true"></span>
      <p class="quote-text"><span class="q q-open">“</span>The only constant is change.<span class="q q-close">”</span></p>
      <p class="quote-author">- <strong>Helenor Vask</strong></p>
    </li>
    <li class="quote">
      <span class="quote-mark" aria-hidden="true"></span>
      <p class="quote-text"><span class="q q-open">“</span>We are what we repeatedly do. Excellence is not an act, it is a habit.<span class="q q-close">”</span></p>
      <p class="quote-author">- <strong>Arden Tolliver</strong></p>
    </li>
    <li class="quote">
      <span class="quote-mark" aria-hidden="true"></span>
      <p class="quote-text"><span class="q q-open">“</span>Simplicity is the ultimate sophistication.<span class="q q-close">”</span></p>
      <p class="quote-author">- <strong>Lorenzo Davenne</strong></p>
    </li>
    <li class="quote">
      <span class="quote-mark" aria-hidden="true"></span>
      <p class="quote-text"><span class="q q-open">“</span>Life is not fair - get used to it.<span class="q q-close">”</span></p>
      <p class="quote-author">- <strong>Bram Garrity</strong></p>
    </li>
  </ul>
  <div class="back-mark" role="img" aria-label="Plain circle in place of the company emblem"></div>
</section>

</body>
</html>
```